Graphics for New Online Software

Looking at a designer to design a UI/UX Interface for an Online Events Platform (just JPEG) and some corresponding images for a website content (i.e. features etc)

Deliverables:
1x User Interface Design for the Platform (refer to attachment)
5-6x Feature Listing Images (refer to attachment)

Target Market(s)

Technology, Online Users Etc

Industry/Entity Type

Software Developer

Number of Pages Required

1 page

Font styles to use
Sans Serif

Colors
34a7d8
0493ce
3176b5
85acd3

Requirements
Must have
• Looks like a well built software - examples:
https://gravelmoor.io/
https://quintaro.com/

All the images should look very professional, as though you are using it on the online platform itself.
Nice to have
• Refer to attached "Feature Listing" and Logo

```html
<!DOCTYPE html>
<html lang="en">
<head>
<meta charset="utf-8">
<title>Eventora – Platform Screens</title>
<link href="https://fonts.googleapis.com/css2?family=Montserrat:wght@400;500;600;700;800&display=swap" rel="stylesheet">
<style>
:root{
  --bg-top:#2a36f0;
  --bg-bottom:#3d80ff;
  --navy:#171a33;
  --ink:#1c1f3a;
  --muted:#8a8fa8;
  --line:#e6e9f2;
  --white:#ffffff;
  --blue:#2e5bff;
  --blue-soft:#e8eeff;
  --tile-a:#a9b3ff;
  --tile-b:#c9d0f5;
  --tile-c:#8e9bff;
}
*{box-sizing:border-box;margin:0;padding:0}
html,body{width:1200px;height:2244px;overflow:hidden}
body{
  font-family:"Montserrat",Arial,sans-serif;
  background:linear-gradient(160deg,var(--bg-top),var(--bg-bottom));
  position:relative;color:var(--ink);
}
.screen{position:absolute;left:88px;width:1024px;background:var(--navy);overflow:hidden;box-shadow:0 20px 40px rgba(10,20,90,.35)}
.screen--people{top:8px;height:740px}
.screen--stage{top:764px;height:820px}
.screen--breakouts{top:1620px;height:560px}

.topbar{position:absolute;left:0;top:0;width:100%;height:72px;background:var(--white);display:flex;align-items:center;justify-content:space-between;padding:0 28px;border-bottom:1px solid var(--line)}
.brand{display:flex;align-items:center;gap:10px;font-weight:800;font-size:26px;letter-spacing:-.5px;color:var(--ink)}
.brand-dot{width:14px;height:14px;border-radius:50%;background:var(--blue)}
.timer{font-size:14px;font-weight:700;color:var(--ink);letter-spacing:.3px}

.sidebar{position:absolute;left:0;top:72px;width:170px;bottom:48px;background:var(--white);padding:18px 12px}
.nav-item{display:flex;align-items:center;gap:10px;height:40px;padding:0 10px;border-radius:8px;font-size:11px;font-weight:700;color:var(--ink);text-transform:uppercase;margin-bottom:10px;line-height:1.2}
.nav-item svg{flex:none;width:18px;height:18px;stroke:var(--blue);fill:none;stroke-width:2}
.nav-item.is-active{background:var(--blue-soft);color:var(--blue)}
.nav-item.tall{height:52px}

.footer{position:absolute;left:0;bottom:0;width:100%;height:48px;background:var(--navy);display:flex;align-items:center;justify-content:space-between;padding:0 28px;font-size:10px;color:#b7bbd3}
.footer-tools{display:flex;gap:14px;align-items:center}
.footer-tools span{width:16px;height:16px;border:2px solid #b7bbd3;border-radius:50%}
.footer-tools span.sq{border-radius:3px}

/* attendees grid */
.attendee-grid{position:absolute;left:182px;top:82px;right:12px;display:grid;grid-template-columns:repeat(4,1fr);grid-auto-rows:196px;gap:10px}
.attendee{position:relative;border-radius:4px;background:linear-gradient(170deg,var(--tile-b),var(--tile-a))}
.attendee:nth-child(3n+2){background:linear-gradient(170deg,#e4e7f4,#c7ccdf)}
.attendee:nth-child(4n+3){background:linear-gradient(170deg,var(--tile-a),var(--tile-c))}
.attendee-name{position:absolute;right:10px;bottom:10px;background:var(--white);border-radius:10px;padding:3px 10px;font-size:9px;font-weight:700;text-transform:uppercase}

/* stage */
.stage-video{position:absolute;left:186px;top:86px;width:530px;height:360px;border-radius:4px;background:linear-gradient(150deg,#eef0f6,#c4c8d6 60%,#a7acbf)}
.play{position:absolute;left:50%;top:50%;width:72px;height:72px;margin:-36px 0 0 -36px;border-radius:50%;background:var(--blue);display:flex;align-items:center;justify-content:center}
.chat{position:absolute;left:730px;top:86px;width:270px;height:360px;background:var(--white);border-radius:6px;padding:12px}
.chat-tabs{display:flex;gap:6px;margin-bottom:12px}
.chat-tab{flex:1;text-align:center;font-size:10px;font-weight:700;padding:6px 0;border-radius:12px;background:#f1f3f9;color:var(--muted)}
.chat-tab.is-active{background:var(--blue);color:var(--white)}
.message{display:flex;gap:8px;margin-bottom:12px}
.avatar{flex:none;width:26px;height:26px;border-radius:50%;background:#c9cfe6}
.message-name{font-size:10px;font-weight:700;color:var(--blue)}
.message-text{font-size:9px;color:var(--muted);line-height:1.4}
.chat-input{position:absolute;left:12px;right:12px;bottom:12px;height:30px;border:1px solid var(--line);border-radius:15px;display:flex;align-items:center;justify-content:space-between;padding:0 4px 0 12px;font-size:9px;color:var(--muted)}
.send{background:var(--blue);color:var(--white);font-weight:700;border-radius:12px;padding:5px 12px}

.agenda{position:absolute;left:186px;top:460px;width:814px;height:300px;background:var(--white);border-radius:4px;padding:22px 20px}
.agenda-title{font-size:28px;font-weight:800;color:var(--blue);margin-bottom:20px}
.agenda-list{display:grid;grid-template-columns:repeat(5,1fr);gap:12px}
.session{border:1px solid var(--line);border-radius:6px;padding:14px 12px;height:190px;box-shadow:0 4px 10px rgba(30,40,90,.06)}
.session-head{display:flex;align-items:center;gap:8px;margin-bottom:14px}
.session-head .avatar{width:32px;height:32px}
.speaker{background:var(--blue-soft);color:var(--blue);border-radius:10px;padding:4px 8px;font-size:9px;font-weight:700;white-space:nowrap}
.session-text{font-size:9px;color:var(--muted);line-height:1.5}

/* breakouts */
.rooms{position:absolute;left:196px;top:90px;width:790px;display:grid;grid-template-columns:1fr 1fr;gap:18px}
.room{background:var(--white);border-radius:4px;overflow:hidden;height:400px;text-align:center}
.room-photo{height:196px;background:linear-gradient(160deg,#8a7666,#4c4a55 60%,#2e3040)}
.room-photo.crowd{background:linear-gradient(160deg,#7e8aa4,#55607a 55%,#39405a)}
.room-date{font-size:12px;font-weight:700;margin-top:22px}
.room-title{font-size:22px;font-weight:800;margin-top:14px}
.room-time{font-size:13px;font-weight:700;color:var(--blue);margin-top:12px}
.room-btn{display:inline-block;margin-top:18px;background:var(--blue);color:var(--white);font-size:10px;font-weight:700;padding:11px 30px;border-radius:20px}
</style>
</head>
<body>

<section class="screen screen--people">
  <header class="topbar"><div class="brand"><span class="brand-dot"></span>Eventora</div><div class="timer">EVENT DURATION (REMAINING 04:30)</div></header>
  <nav class="sidebar">
    <div class="nav-item is-active"><svg viewBox="0 0 20 20"><circle cx="10" cy="10" r="8"/><path d="M10 9v5M10 6v1"/></svg>Event Info</div>
    <div class="nav-item"><svg viewBox="0 0 20 20"><rect x="2" y="4" width="16" height="11" rx="2"/><path d="M7 18h6"/></svg>Stage</div>
    <div class="nav-item"><svg viewBox="0 0 20 20"><rect x="2" y="3" width="7" height="7" rx="1"/><rect x="11" y="10" width="7" height="7" rx="1"/></svg>Breakouts</div>
    <div class="nav-item tall"><svg viewBox="0 0 20 20"><path d="M3 17V8l7-5 7 5v9z"/></svg>Virtual<br>Exhibition</div>
    <div class="nav-item"><svg viewBox="0 0 20 20"><path d="M2 17L10 3l8 14z"/></svg>Booths</div>
    <div class="nav-item"><svg viewBox="0 0 20 20"><path d="M10 2l2.4 5 5.6.6-4.2 3.8 1.2 5.6L10 14.2 5 17l1.2-5.6L2 7.6 7.6 7z"/></svg>Rewards</div>
  </nav>
  <div class="attendee-grid">
    <div class="attendee" role="img" aria-label="Attendee video tile"><span class="attendee-name">Marcus</span></div>
    <div class="attendee" role="img" aria-label="Attendee video tile"><span class="attendee-name">Leona</span></div>
    <div class="attendee" role="img" aria-label="Attendee video tile"><span class="attendee-name">Tomas</span></div>
    <div class="attendee" role="img" aria-label="Attendee video tile"><span class="attendee-name">Helena</span></div>
    <div class="attendee" role="img" aria-label="Attendee video tile"><span class="attendee-name">Oliver</span></div>
    <div class="attendee" role="img" aria-label="Attendee video tile"><span class="attendee-name">Priya</span></div>
    <div class="attendee" role="img" aria-label="Attendee video tile"><span class="attendee-name">Daniel</span></div>
    <div class="attendee" role="img" aria-label="Attendee video tile"><span class="attendee-name">Clara</span></div>
    <div class="attendee" role="img" aria-label="Attendee video tile"><span class="attendee-name">Monica</span></div>
    <div class="attendee" role="img" aria-label="Attendee video tile"><span class="attendee-name">Ethan</span></div>
    <div class="attendee" role="img" aria-label="Attendee video tile"><span class="attendee-name">Jonas</span></div>
    <div class="attendee" role="img" aria-label="Attendee video tile"><span class="attendee-name">Sofia</span></div>
  </div>
  <footer class="footer"><span>Eventora ©2020 All Rights Reserved | Privacy Statement | Site Map</span><div class="footer-tools"><span></span><span class="sq"></span><span></span><span class="sq"></span><span></span></div></footer>
</section>

<section class="screen screen--stage">
  <header class="topbar"><div class="brand"><span class="brand-dot"></span>Eventora</div><div class="timer">EVENT DURATION (REMAINING 04:30)</div></header>
  <nav class="sidebar">
    <div class="nav-item"><svg viewBox="0 0 20 20"><circle cx="10" cy="10" r="8"/><path d="M10 9v5M10 6v1"/></svg>Event Info</div>
    <div class="nav-item is-active"><svg viewBox="0 0 20 20"><rect x="2" y="4" width="16" height="11" rx="2"/><path d="M7 18h6"/></svg>Stage</div>
    <div class="nav-item"><svg viewBox="0 0 20 20"><rect x="2" y="3" width="7" height="7" rx="1"/><rect x="11" y="10" width="7" height="7" rx="1"/></svg>Breakouts</div>
    <div class="nav-item tall"><svg viewBox="0 0 20 20"><path d="M3 17V8l7-5 7 5v9z"/></svg>Virtual<br>Exhibition</div>
    <div class="nav-item"><svg viewBox="0 0 20 20"><path d="M2 17L10 3l8 14z"/></svg>Booths</div>
    <div class="nav-item"><svg viewBox="0 0 20 20"><path d="M10 2l2.4 5 5.6.6-4.2 3.8 1.2 5.6L10 14.2 5 17l1.2-5.6L2 7.6 7.6 7z"/></svg>Rewards</div>
  </nav>
  <div class="stage-video" role="img" aria-label="Live keynote speaker on stage">
    <div class="play"><svg width="26" height="26" viewBox="0 0 26 26"><path d="M8 5l14 8-14 8z" fill="#fff"/></svg></div>
  </div>
  <aside class="chat">
    <div class="chat-tabs"><span class="chat-tab is-active">CHAT</span><span class="chat-tab">Q&amp;A</span><span class="chat-tab">POLLS</span></div>
    <div class="message"><span class="avatar"></span><div><div class="message-name">Amelia</div><div class="message-text">Great session so far, loving the insights here.</div></div></div>
    <div class="message"><span class="avatar"></span><div><div class="message-name">Ravi Kumar</div><div class="message-text">Can we get the slides after the talk?</div></div></div>
    <div class="message"><span class="avatar"></span><div><div class="message-name">Sandra</div><div class="message-text">Audio is crystal clear on my side.</div></div></div>
    <div class="message"><span class="avatar"></span><div><div class="message-name">Leonie</div><div class="message-text">Looking forward to the next speaker panel.</div></div></div>
    <div class="chat-input"><span>Write here...</span><span class="send">Send</span></div>
  </aside>
  <section class="agenda">
    <h2 class="agenda-title">The Agenda</h2>
    <div class="agenda-list">
      <article class="session"><div class="session-head"><span class="avatar"></span><span class="speaker">Daniel Ortiz</span></div><div class="session-text">Opening keynote on the future of live digital events.</div></article>
      <article class="session"><div class="session-head"><span class="avatar"></span><span class="speaker">Nora Blake</span></div><div class="session-text">Building engaged audiences across global virtual stages today.</div></article>
      <article class="session"><div class="session-head"><span class="avatar"></span><span class="speaker">Ivan Petrov</span></div><div class="session-text">Panel on networking tools for remote event teams.</div></article>
      <article class="session"><div class="session-head"><span class="avatar"></span><span class="speaker">Mia Chen</span></div><div class="session-text">Workshop on sponsor booths and lead capture flows.</div></article>
      <article class="session"><div class="session-head"><span class="avatar"></span><span class="speaker">Lucas Reid</span></div><div class="session-text">Closing remarks and rewards for our most active guests.</div></article>
    </div>
  </section>
  <footer class="footer"><span>Eventora ©2020 All Rights Reserved | Privacy Statement | Site Map</span><div class="footer-tools"><span></span><span class="sq"></span><span></span><span class="sq"></span><span></span></div></footer>
</section>

<section class="screen screen--breakouts">
  <header class="topbar"><div class="brand"><span class="brand-dot"></span>Eventora</div><div class="timer">EVENT DURATION (REMAINING 04:30)</div></header>
  <nav class="sidebar">
    <div class="nav-item"><svg viewBox="0 0 20 20"><circle cx="10" cy="10" r="8"/><path d="M10 9v5M10 6v1"/></svg>Event Info</div>
    <div class="nav-item"><svg viewBox="0 0 20 20"><rect x="2" y="4" width="16" height="11" rx="2"/><path d="M7 18h6"/></svg>Stage</div>
    <div class="nav-item is-active"><svg viewBox="0 0 20 20"><rect x="2" y="3" width="7" height="7" rx="1"/><rect x="11" y="10" width="7" height="7" rx="1"/></svg>Breakouts</div>
    <div class="nav-item tall"><svg viewBox="0 0 20 20"><path d="M3 17V8l7-5 7 5v9z"/></svg>Virtual<br>Exhibition</div>
    <div class="nav-item"><svg viewBox="0 0 20 20"><path d="M2 17L10 3l8 14z"/></svg>Booths</div>
    <div class="nav-item"><svg viewBox="0 0 20 20"><path d="M10 2l2.4 5 5.6.6-4.2 3.8 1.2 5.6L10 14.2 5 17l1.2-5.6L2 7.6 7.6 7z"/></svg>Rewards</div>
  </nav>
  <div class="rooms">
    <article class="room">
      <div class="room-photo" role="img" aria-label="Lounge meeting room interior"></div>
      <div class="room-date">11/05</div>
      <div class="room-title">JOIN BREAKOUT ROOM 1</div>
      <div class="room-time">3.00PM TO 4.30PM</div>
      <span class="room-btn">3RD PARTY VIDEO ROOM</span>
    </article>
    <article class="room">
      <div class="room-photo crowd" role="img" aria-label="Conference audience in a hall"></div>
      <div class="room-date">11/05</div>
      <div class="room-title">JOIN BREAKOUT ROOM 2</div>
      <div class="room-time">3.00PM TO 4.30PM</div>
      <span class="room-btn">3RD PARTY VIDEO ROOM</span>
    </article>
  </div>
  <footer class="footer"><span>Eventora ©2020 All Rights Reserved | Privacy Statement | Site Map</span><div class="footer-tools"><span></span><span class="sq"></span><span></span><span class="sq"></span><span></span></div></footer>
</section>

</body>
</html>
```